Business Card Design

Looking for business card designs for a new business. there will be two cards of the same design (both lots of information below in contact info). We would like the logo diagonally across the card with the information split above and below the logo similar to sketch. happy to look at similar alternatives
Please use same colours as in logo design

Industry/Entity Type

Business

Contact Information for Business Card

Dwight Halloran
mob - 0491 738 204
ph - 02 6148 3920
fax - 02 6148 3975
email - dwight@kestrelbeams.com.au
14 Larkmoor Road, Corrabin NSW 2381

Colin Marchetti
mob - 0438 912 557
ph - 02 6148 3920
fax - 02 6148 3975
email - colin@kestrelbeams.com.au

```html
<!DOCTYPE html>
<html lang="en">
<head>
<meta charset="utf-8">
<title>Kestrel Beams – Business Cards</title>
<link rel="stylesheet" href="https://fonts.googleapis.com/css2?family=Questrial&family=Roboto+Condensed:wght@700&display=swap">
<style>
  :root {
    --teal: #1b8b8b;
    --ink: #141414;
    --paper: #ffffff;
    --backdrop: #ebe7e1;
    --shadow: rgba(0,0,0,0.28);
  }
  * { margin: 0; padding: 0; box-sizing: border-box; }
  html, body {
    width: 1200px; height: 1013px; overflow: hidden;
    background: var(--backdrop);
    font-family: "Questrial", sans-serif;
  }
  .card {
    position: absolute;
    width: 640px; height: 390px;
    overflow: hidden;
    box-shadow: 0 10px 28px var(--shadow);
  }
  .card--front { left: 120px; top: 70px; background: var(--paper); }
  .card--back { left: 440px; top: 560px; background: var(--teal); }

  .card__shapes { position: absolute; inset: 0; width: 100%; height: 100%; }

  .card__name {
    position: absolute; left: 22px; top: 13px;
    font-family: "Roboto Condensed", sans-serif; font-weight: 700;
    font-size: 25px; letter-spacing: 0.5px;
    color: var(--paper); text-transform: uppercase;
  }

  .contact {
    position: absolute;
    font-size: 16px; color: var(--ink);
    line-height: 1.6;
  }
  .contact--personal { left: 22px; top: 78px; }
  .contact--office { left: 410px; top: 258px; }
  .contact__row { display: flex; align-items: flex-start; gap: 8px; }
  .contact__icon { width: 14px; height: 14px; margin-top: 5px; flex: none; fill: var(--ink); }
  .contact--office .contact__icon { fill: var(--teal); }

  .brand {
    position: absolute;
    display: flex; align-items: center; gap: 14px;
    white-space: nowrap;
  }
  .brand__mark { width: 30px; height: 30px; flex: none; }
  .brand__name { font-family: "Questrial", sans-serif; font-size: 54px; line-height: 1; }

  .brand--front { left: 130px; top: 160px; transform: rotate(-22deg); }
  .brand--front .brand__mark { background: var(--teal); }
  .brand--front .brand__name { color: var(--ink); }

  .brand--back { left: 50%; top: 50%; transform: translate(-50%, -50%); }
  .brand--back .brand__mark { background: var(--paper); }
  .brand--back .brand__name { color: var(--paper); font-size: 62px; }
</style>
</head>
<body>

<section class="card card--front" aria-label="Business card front">
  <svg class="card__shapes" viewBox="0 0 640 390" aria-hidden="true">
    <path d="M0 0 H640 V150 Q625 62 560 58 H0 Z" fill="var(--ink)"/>
    <path d="M0 250 Q20 298 95 292 L92 300 Q20 306 0 262 Z" fill="var(--ink)"/>
    <path d="M0 262 Q20 306 92 300 Q150 298 175 350 L260 390 H0 Z" fill="var(--teal)"/>
  </svg>

  <h1 class="card__name">Dwight Halloran</h1>

  <div class="contact contact--personal">
    <div class="contact__row">
      <svg class="contact__icon" viewBox="0 0 14 14"><rect x="3" y="0" width="8" height="14" rx="1.5"/></svg>
      <span>0491 738 204</span>
    </div>
    <div class="contact__row">
      <svg class="contact__icon" viewBox="0 0 14 14"><rect x="0" y="2" width="14" height="10" rx="1"/></svg>
      <span>dwight@kestrelbeams.com.au</span>
    </div>
  </div>

  <div class="brand brand--front">
    <span class="brand__mark" aria-hidden="true"></span>
    <span class="brand__name">Kestrel Beams</span>
  </div>

  <div class="contact contact--office">
    <div class="contact__row">
      <svg class="contact__icon" viewBox="0 0 14 14"><path d="M3 0 L6 3 L4.5 5 Q6 8.5 9 9.5 L11 8 L14 11 L12 14 Q3 13 0 3 Z"/></svg>
      <span>02 6148 3920</span>
    </div>
    <div class="contact__row">
      <svg class="contact__icon" viewBox="0 0 14 14"><rect x="0" y="5" width="14" height="8" rx="1"/><rect x="3" y="1" width="8" height="5"/></svg>
      <span>02 6148 3975</span>
    </div>
    <div class="contact__row">
      <svg class="contact__icon" viewBox="0 0 14 14"><path d="M7 0 A5 5 0 0 1 12 5 C12 9 7 14 7 14 C7 14 2 9 2 5 A5 5 0 0 1 7 0 Z"/></svg>
      <span>14 Larkmoor Road<br>Corrabin NSW 2381</span>
    </div>
  </div>
</section>

<section class="card card--back" aria-label="Business card back">
  <div class="brand brand--back">
    <span class="brand__mark" aria-hidden="true"></span>
    <span class="brand__name">Kestrel Beams</span>
  </div>
</section>

</body>
</html>
```